Ad design for magazines to promote our Cloud Computing Consulting Company Branding

We need an advertisement design to promote our brand online and on printed magazines (full page). We are a cloud consulting company (products & services on the Cloud) and would like to create an ad that conveys confidence in our services.
Some of the ideas we would want to project are:
First Spanish consulting company specialized in Cloud Computing Technology and Services
We help you incorporate into your business the best Cloud Computing Solutions on the market to improve efficiency, reduce costs and increase competitiveness
Experts in:
• Cloud infrastructure modernization
• Digital Transformation, productivity and collaboration
• Cloud data management
• Advanced analytics
• Cloud application development
• Location Strategy
We are Norvane Sky Ally Prime and have recently achieved a Task Renewal Mastery award
We are also partners of other leading technologies
We have a web page to be used as reference even though we are open to designs that differ from this style. www.brevoltaconsult.example
Target Market(s)
B2B Market Business to Business
Requirements
Must have
- Dimensions: 21x29.7 cm. (width by height) CMYK, 300 dpi, 3 millimeters of bleed and cut lines
Nice to have
- We would like an attractive image with not a lot of text (just about what is on the explanation), including the Ally Prime and Task Renewal badges.

```html
<!DOCTYPE html>
<html lang="en">
<head>
<meta charset="utf-8">
<title>Brevolta Consult – Cloud Computing Magazine Ad</title>
<link rel="stylesheet" href="https://fonts.googleapis.com/css2?family=Montserrat:wght@300;400;600;700;800&display=swap">
<style>
  :root {
    --page-bg: #ffffff;
    --navy: #0c1231;
    --navy-deep: #080c24;
    --plum: #3a0e2e;
    --teal: #2fc6c8;
    --red: #e3212b;
    --white: #ffffff;
    --line: #2fb9bd;
    --ring-dark: #1b2346;
  }
  html, body {
    margin: 0;
    padding: 0;
    width: 1200px;
    height: 2591px;
    overflow: hidden;
    background: var(--page-bg);
  }
  .ad {
    position: absolute;
    left: 40px;
    top: 501px;
    width: 842px;
    height: 1194px;
    transform: scale(1.33);
    transform-origin: 0 0;
    overflow: hidden;
    font-family: "Montserrat", sans-serif;
    color: var(--white);
    background:
      radial-gradient(ellipse 420px 300px at 100% 0%, rgba(110,20,70,.75), transparent 70%),
      radial-gradient(ellipse 500px 260px at 90% 100%, rgba(90,16,55,.7), transparent 70%),
      linear-gradient(160deg, var(--navy-deep) 0%, var(--navy) 55%, #1a1036 100%);
    box-shadow: 0 6px 18px rgba(0,0,0,.35);
  }
  .headline {
    position: absolute;
    left: 58px;
    top: 56px;
    margin: 0;
    line-height: 1.12;
  }
  .headline-light {
    display: block;
    font-weight: 300;
    font-size: 45px;
    letter-spacing: 1.5px;
  }
  .headline-accent {
    display: block;
    font-weight: 800;
    font-size: 38px;
    color: var(--teal);
    line-height: 1.28;
    margin-top: 4px;
  }
  .intro {
    position: absolute;
    left: 58px;
    top: 294px;
    width: 540px;
    margin: 0;
    font-size: 20px;
    line-height: 1.28;
    font-weight: 400;
  }
  .intro strong { color: var(--red); font-weight: 700; }
  .illustration {
    position: absolute;
    left: 400px;
    top: 350px;
    width: 400px;
    height: 430px;
    background:
      radial-gradient(ellipse 170px 120px at 55% 70%, rgba(47,198,200,.55), transparent 75%),
      radial-gradient(ellipse 120px 180px at 62% 35%, rgba(88,70,200,.55), transparent 75%);
  }
  .timeline {
    position: absolute;
    left: 0;
    top: 0;
    width: 842px;
    height: 1194px;
  }
  .experts-tag {
    position: absolute;
    left: 183px;
    top: 439px;
    height: 35px;
    padding: 0 18px 0 14px;
    line-height: 35px;
    background: var(--red);
    border-radius: 0 18px 18px 0;
    font-size: 17px;
    font-weight: 600;
  }
  .service {
    position: absolute;
    font-size: 16.5px;
    line-height: 1.25;
    font-weight: 400;
    margin: 0;
  }
  .service--side { left: 178px; }
  .service--bottom { width: 170px; text-align: center; top: 900px; }
  .badge {
    position: absolute;
    left: 65px;
    top: 1017px;
    width: 120px;
    height: 120px;
    border-radius: 50%;
    background: var(--white);
  }
  .brand {
    position: absolute;
    left: 226px;
    top: 1058px;
    display: flex;
    align-items: center;
    gap: 12px;
  }
  .brand-mark {
    width: 30px;
    height: 30px;
    background: var(--red);
  }
  .brand-name {
    font-size: 20px;
    font-weight: 700;
    letter-spacing: 1.5px;
    color: var(--red);
    text-transform: uppercase;
  }
  .web-bar {
    position: absolute;
    left: 560px;
    top: 1067px;
    width: 282px;
    height: 34px;
    background: var(--teal);
    color: var(--navy);
    font-size: 12.5px;
    font-weight: 700;
    line-height: 34px;
    padding-left: 12px;
    box-sizing: border-box;
    letter-spacing: .4px;
  }
</style>
</head>
<body>
<main class="ad">
  <h1 class="headline">
    <span class="headline-light">FIRST SPANISH CONSULTING</span>
    <span class="headline-light">COMPANY SPECIALIZED IN</span>
    <span class="headline-accent">CLOUD COMPUTING TECHNOLOGY<br>AND SERVICES</span>
  </h1>

  <p class="intro">We help you incorporate into your business the best Cloud Computing Solutions on the market <strong>to improve efficiency, reduce costs and increase competitiveness</strong></p>

  <div class="illustration" role="img" aria-label="Isometric illustration of a consultant standing beside a tall server screen with login panel, a cloud and data blocks on a glowing platform"></div>

  <svg class="timeline" viewBox="0 0 842 1194" aria-hidden="true">
    <g fill="none" stroke="var(--line)" stroke-width="2">
      <polyline points="183,456 100,456 100,857 782,857"/>
    </g>
    <g fill="var(--line)">
      <circle cx="100" cy="635" r="4"/>
      <circle cx="258" cy="857" r="4"/>
      <circle cx="443" cy="857" r="4"/>
      <circle cx="626" cy="857" r="4"/>
      <circle cx="782" cy="857" r="4"/>
    </g>
    <g id="rings">
      <g transform="translate(100,554)"><circle r="45" fill="var(--ring-dark)"/><circle r="38" fill="var(--white)" stroke="var(--red)" stroke-width="5"/></g>
      <g transform="translate(100,715)"><circle r="45" fill="var(--ring-dark)"/><circle r="38" fill="var(--white)" stroke="var(--red)" stroke-width="5"/></g>
      <g transform="translate(167,857)"><circle r="45" fill="var(--ring-dark)"/><circle r="38" fill="var(--white)" stroke="var(--red)" stroke-width="5"/></g>
      <g transform="translate(350,857)"><circle r="45" fill="var(--ring-dark)"/><circle r="38" fill="var(--white)" stroke="var(--red)" stroke-width="5"/></g>
      <g transform="translate(535,857)"><circle r="45" fill="var(--ring-dark)"/><circle r="38" fill="var(--white)" stroke="var(--red)" stroke-width="5"/></g>
      <g transform="translate(716,857)"><circle r="45" fill="var(--ring-dark)"/><circle r="38" fill="var(--white)" stroke="var(--red)" stroke-width="5"/></g>
    </g>
    <g fill="none" stroke="var(--navy)" stroke-width="1.6" stroke-linecap="round" stroke-linejoin="round">
      <!-- cloud network -->
      <g transform="translate(100,554)">
        <path d="M-9,-6 a6,6 0 0 1 3,-11 a8,8 0 0 1 14,2 a5,5 0 0 1 1,9 z"/>
        <path d="M0,-6 v6 M-10,0 h20 M-10,0 v5 M10,0 v5"/>
        <rect x="-16" y="5" width="11" height="9"/><rect x="5" y="5" width="11" height="8"/>
      </g>
      <!-- laptop -->
      <g transform="translate(100,715)">
        <rect x="-13" y="-10" width="26" height="17"/>
        <path d="M-17,9 h34 l-3,4 h-28 z M-7,-5 h6 v8 h-6 z M3,-5 h6 M3,-1 h6"/>
      </g>
      <!-- data laptop -->
      <g transform="translate(167,857)">
        <rect x="-13" y="-8" width="26" height="16"/>
        <path d="M-17,10 h34 M-5,-12 a5,5 0 0 1 10,0 v8 h-10 z M-2,-2 v4 M2,-4 v6"/>
      </g>
      <!-- analytics funnel gear -->
      <g transform="translate(350,857)">
        <path d="M-2,-15 h16 l-6,9 v8 l-4,2 v-10 z"/>
        <circle cx="-5" cy="6" r="6"/><circle cx="-5" cy="6" r="2"/>
      </g>
      <!-- app device -->
      <g transform="translate(535,857)">
        <rect x="-9" y="-15" width="18" height="28" rx="2"/>
        <path d="M-4,-3 a4,4 0 0 1 8,0 a3,3 0 0 1 0,6 h-8 a3,3 0 0 1 0,-6 M-2,9 h4"/>
      </g>
      <!-- location board -->
      <g transform="translate(716,857)">
        <rect x="-13" y="-14" width="26" height="18"/>
        <path d="M-8,4 l-4,11 M8,4 l4,11 M-16,15 h32 M0,-10 a4,4 0 0 1 4,4 c0,3 -4,7 -4,7 c0,0 -4,-4 -4,-7 a4,4 0 0 1 4,-4"/>
      </g>
    </g>
  </svg>

  <div class="experts-tag">Experts in:</div>

  <p class="service service--side" style="top:532px;">Cloud infrastructure<br>modernization</p>
  <p class="service service--side" style="top:682px;">Digital Transformation,<br>productivity and<br>collaboration</p>
  <p class="service service--bottom" style="left:82px;">Cloud data<br>management</p>
  <p class="service service--bottom" style="left:265px;">Advanced<br>analytics</p>
  <p class="service service--bottom" style="left:440px;">Cloud application<br>development</p>
  <p class="service service--bottom" style="left:631px;">Location Strategy</p>

  <div class="badge" role="img" aria-label="Task Renewal Mastery badge from Norvane Sky"></div>

  <div class="brand">
    <span class="brand-mark"></span>
    <span class="brand-name">Brevolta Consult</span>
  </div>

  <div class="web-bar">www.brevoltaconsult.example</div>
</main>
</body>
</html>
```